Can you make our site AWESOME?

Hi Guys,

I am a co-founder of Tallow Crate Rentals Australia, the world's first e-commerce skip bin business.

We are looking to update our site before a launch into the UK in March.

Please help us by submitting your designs for the following pages:

- Home page (www.tallowcraterentals.example.au)
- About us (https://www.tallowcraterentals.example.au/pages/about-us
- Contact us (https://www.tallowcraterentals.example.au/pages/contact-us)
- Quick Quote / Pricing (https://www.tallowcraterentals.example.au/pages/free-instant-quote-skip-bin-hire)

NOTES:
- Design should be high-converting
- best designs will be fresh, modern, easy to read, distinctive and memorable
- please use our logo and video colours
- feel free to change logos, layout, images and anything else you feel can be improved
- the winning designer will potentially have the opportunity to re-design the other pages on our site
- brief is for design only

Any questions just ask.

Thanks,
Oliver

```html
<!DOCTYPE html>
<html lang="en">
<head>
<meta charset="utf-8">
<title>Tallow Crate Rentals Australia</title>
<link href="https://fonts.googleapis.com/css2?family=Lato:wght@400;700;900&display=swap" rel="stylesheet">
<style>
:root{
  --navy:#2b2d6e;
  --navy-deep:#1f2158;
  --green:#2f7d3b;
  --green-bright:#3a9a47;
  --lavender:#e5e5f1;
  --ink:#3d3f55;
  --muted:#6b6d80;
  --white:#ffffff;
  --star:#f2a516;
}
*{box-sizing:border-box;margin:0;padding:0}
html,body{width:1200px;height:3774px;overflow:hidden}
body{position:relative;background:var(--white);font-family:'Lato',sans-serif;color:var(--ink)}
.abs{position:absolute}
svg{display:block}

/* header */
.site-header{left:0;top:0;width:1200px;height:95px;background:var(--white);z-index:5}
.brand{left:143px;top:26px;display:flex;align-items:center;gap:12px}
.brand-mark{width:40px;height:40px;background:var(--navy);border-radius:4px}
.brand-name{font-weight:900;font-size:19px;line-height:21px;color:var(--navy);letter-spacing:1px;width:230px}
.main-nav{left:490px;top:38px;display:flex;gap:24px;font-size:15px;color:var(--navy)}
.btn-login{left:865px;top:30px;width:82px;height:36px;border-radius:18px;background:var(--green);color:#fff;font-size:13px;font-weight:700;display:flex;align-items:center;justify-content:center}
.btn-signup{left:952px;top:30px;width:86px;height:36px;border-radius:18px;border:2px solid var(--navy);color:var(--navy);font-size:13px;font-weight:700;display:flex;align-items:center;justify-content:center}
.cart{left:1050px;top:32px}

/* hero */
.hero-photo{left:0;top:95px;width:1200px;height:680px;background:linear-gradient(180deg,#5d6198 0%,#3a3d7c 45%,#2b2d6e 100%)}
.hero-title{left:0;top:236px;width:1200px;text-align:center;color:#fff;font-weight:900;font-size:40px}
.hero-sub{left:0;top:292px;width:1200px;text-align:center;color:#fff;font-size:24px;letter-spacing:.5px}
.search{height:56px;background:#fff;border-radius:28px;display:flex;align-items:center;justify-content:space-between;padding:0 8px 0 32px;box-shadow:0 4px 14px rgba(0,0,0,.18)}
.search span{font-size:19px;color:var(--muted)}
.search b{background:var(--green);color:#fff;font-size:19px;font-weight:700;height:42px;width:130px;border-radius:21px;display:flex;align-items:center;justify-content:center}
.hero-search{left:302px;top:350px;width:601px}
.btn-call{left:443px;top:430px;width:317px;height:51px;border-radius:26px;background:var(--green-bright);color:#fff;font-size:21px;display:flex;align-items:center;justify-content:center;gap:8px}
.hero-wave{left:0;top:560px}

/* categories */
.cat{width:164px;height:160px;background:#fff;box-shadow:0 6px 18px rgba(30,30,80,.22);display:flex;flex-direction:column;align-items:center;justify-content:center;gap:14px;font-size:19px;font-weight:700;color:var(--green)}

/* intro */
.video{left:133px;top:876px;width:476px;height:301px;background:linear-gradient(135deg,#c9ccd8,#6b6f97 60%,#3a3d6c)}
.play{left:337px;top:982px}
.intro-title{left:657px;top:882px;font-size:37px;font-weight:900;color:var(--navy);letter-spacing:1px}
.intro-text{left:661px;top:950px;width:410px;font-size:15.5px;line-height:22px;color:var(--muted)}
.intro-text p+p{margin-top:10px}
.btn-outline{border:2px solid var(--navy);color:var(--navy);border-radius:28px;display:flex;align-items:center;justify-content:center;font-size:19px}

/* how it works */
.how-bg{left:0;top:1290px}
.how-title{left:0;top:1428px;width:1200px;text-align:center;font-size:30px;font-weight:900;color:var(--navy)}
.step-num{font-size:78px;font-weight:300;color:var(--navy);line-height:1}
.step-head{font-size:19px;font-weight:700;color:var(--green)}
.step-text{font-size:12.5px;line-height:15px;color:var(--muted)}

/* save */
.save-bg{left:0;top:1790px}
.save-title{left:120px;top:2008px;width:464px;text-align:center;font-size:29px;font-weight:900;color:#fff}
.save-text{left:135px;top:2062px;width:434px;text-align:center;font-size:14.5px;line-height:25px;color:#fff}
.btn-green{left:272px;top:2211px;width:158px;height:43px;border-radius:22px;background:var(--green-bright);color:#fff;font-size:14px;font-weight:700;display:flex;align-items:center;justify-content:center}
.feature{background:#fff;box-shadow:0 6px 20px rgba(20,20,60,.25);border-radius:4px;display:flex;flex-direction:column;align-items:center;text-align:center;padding:32px 16px 0}
.feature h3{font-size:15.5px;font-weight:900;color:var(--navy);margin-top:18px;line-height:18px}
.feature p{font-size:12.5px;line-height:15px;color:var(--ink);margin-top:8px}

/* testimonials */
.testi-title{left:0;top:2475px;width:1200px;text-align:center;font-size:30px;font-weight:900;color:var(--navy)}
.quote-mark{left:0;top:2520px;width:1200px;text-align:center;font-size:110px;color:#c7c7d6;font-weight:900;line-height:1}
.testi-text{left:225px;top:2610px;width:750px;text-align:center;font-size:17.5px;line-height:31px;color:var(--ink)}
.testi-label{left:0;top:2730px;width:1200px;text-align:center;font-size:19px;font-weight:900;color:var(--navy)}
.stars{left:0;top:2768px;width:1200px;display:flex;justify-content:center;gap:3px}

/* ready */
.ready-bg{left:0;top:2860px}
.ready-title{left:0;top:2978px;width:1200px;text-align:center;font-size:37px;font-weight:900;color:#fff}
.ready-text{left:0;top:3033px;width:1200px;text-align:center;font-size:20px;line-height:34px;color:#fff}
.ready-search{left:307px;top:3127px;width:601px}
.btn-ghost{left:531px;top:3210px;width:146px;height:51px;border:2px solid #fff;border-radius:26px;color:#fff;font-size:18px;display:flex;align-items:center;justify-content:center}

/* footer */
.footer-skyline{left:120px;top:3420px;width:960px;height:230px;background:linear-gradient(180deg,rgba(229,229,241,0) 0%,rgba(229,229,241,.55) 100%)}
.footer-brand{left:158px;top:3426px}
.footer-about{left:164px;top:3486px;width:250px;font-size:14px;line-height:19px;color:var(--muted)}
.footer-col h4{font-size:16px;font-weight:900;color:var(--green);margin-bottom:6px}
.footer-col li{list-style:none;font-size:15px;line-height:26px;color:var(--navy)}
.footer-news p{font-size:13px;line-height:18px;color:var(--ink);width:250px}
.email{left:805px;top:3497px;width:244px;height:36px;border:1.5px solid #b8b9cc;border-radius:18px;font-size:14px;color:#9a9bb0;padding-left:18px;display:flex;align-items:center}
.btn-sub{left:808px;top:3543px;width:125px;height:36px;border-radius:18px;background:var(--navy);color:#fff;font-size:15px;font-weight:700;display:flex;align-items:center;justify-content:center}
.rule{left:0;top:3668px;width:1200px;height:1px;background:#dcdce6}
.copyright{left:0;top:3689px;width:1200px;text-align:center;font-size:14px;color:var(--muted)}
.social{left:0;top:3726px;width:1200px;display:flex;justify-content:center;gap:22px}
.social i{width:20px;height:20px;border-radius:50%;background:var(--green);display:block}
</style>
</head>
<body>

<header class="site-header abs">
  <div class="brand abs"><span class="brand-mark"></span><span class="brand-name">TALLOW CRATE RENTALS AUSTRALIA</span></div>
  <nav class="main-nav abs"><span>PRICING</span><span>ABOUT</span><span>TRADE SECRETS</span><span>CONTACT</span></nav>
  <div class="btn-login abs">LOGIN</div>
  <div class="btn-signup abs">SIGN UP</div>
  <svg class="cart abs" width="30" height="28" viewBox="0 0 30 28" fill="none" stroke="#2f7d3b" stroke-width="2.4"><path d="M1 3h5l4 15h15l3-11H8"/><circle cx="12" cy="24" r="2"/><circle cx="23" cy="24" r="2"/></svg>
</header>

<section class="hero">
  <div class="hero-photo abs" role="img" aria-label="Photo of a residential street with a skip bin, tinted navy"></div>
  <h1 class="hero-title abs">1000'S OF SKIPS AT YOUR FINGER TIPS</h1>
  <p class="hero-sub abs">BEST SERVICE &amp; PRICE | HASSLE FREE | AUSTRALIA WIDE</p>
  <div class="search hero-search abs"><span>Enter Postcode or Suburb</span><b>Search</b></div>
  <div class="btn-call abs"><svg width="20" height="20" viewBox="0 0 24 24" fill="#fff"><path d="M6.6 10.8a15 15 0 006.6 6.6l2.2-2.2a1 1 0 011-.25 11.4 11.4 0 003.6.57 1 1 0 011 1V20a1 1 0 01-1 1A17 17 0 013 4a1 1 0 011-1h3.5a1 1 0 011 1c0 1.25.2 2.45.57 3.57a1 1 0 01-.25 1z"/></svg>Call Us Now 1800 555 019</div>
  <svg class="hero-wave abs" width="1200" height="220" viewBox="0 0 1200 220" preserveAspectRatio="none"><path d="M0 170 C250 210 420 70 650 90 C860 110 980 40 1200 60 L1200 220 L0 220Z" fill="#fff"/></svg>
</section>

<section class="categories">
  <div class="cat abs" style="left:153px;top:581px"><svg width="56" height="50" viewBox="0 0 56 50" fill="none" stroke="#4a4c66" stroke-width="2.5"><path d="M4 24L28 4l24 20M10 19v28h36V19M23 47V32h10v15"/></svg>Renovator</div>
  <div class="cat abs" style="left:342px;top:626px"><svg width="56" height="56" viewBox="0 0 56 56" fill="none" stroke="#2b2d6e" stroke-width="3"><path d="M8 48L40 16M36 8a8 8 0 0012 12l-6-2-4-4z"/><path d="M48 48L16 16M8 8l8 8" stroke="#2f7d3b"/></svg>Tradie</div>
  <div class="cat abs" style="left:528px;top:581px"><svg width="56" height="52" viewBox="0 0 56 52" fill="none" stroke="#4a4c66" stroke-width="2.5"><rect x="4" y="10" width="40" height="36"/><path d="M10 38l10-14 8 8 10-16"/><path d="M44 4l8 8-16 16h-8v-8z" stroke="#2f7d3b"/></svg>Builder</div>
  <div class="cat abs" style="left:717px;top:626px"><svg width="56" height="48" viewBox="0 0 56 48" fill="none" stroke="#4a4c66" stroke-width="2.5"><rect x="4" y="12" width="48" height="32" rx="3"/><path d="M20 12V5h16v7M4 26h48"/><rect x="24" y="22" width="8" height="8" fill="#2f7d3b" stroke="none"/></svg>Corporate</div>
  <div class="cat abs" style="left:903px;top:581px"><svg width="54" height="54" viewBox="0 0 54 54" fill="none" stroke="#2f7d3b" stroke-width="2.5"><circle cx="27" cy="27" r="23"/><ellipse cx="27" cy="27" rx="10" ry="23"/><path d="M4 27h46M8 15h38M8 39h38"/></svg>National</div>
</section>

<section class="intro">
  <div class="video abs" role="img" aria-label="Explainer video still: animated character in front of a house"></div>
  <svg class="play abs" width="70" height="70" viewBox="0 0 70 70"><circle cx="35" cy="35" r="32" fill="rgba(255,255,255,.85)" stroke="#fff" stroke-width="3"/><path d="M28 22l20 13-20 13z" fill="#444"/></svg>
  <h2 class="intro-title abs">SKIP BIN HIRE</h2>
  <div class="intro-text abs">
    <p>Pellentesque faucibus Ut accumsan ultricies elit Maecenas at justo id velit placerat molestie</p>
    <p>Mauris nunc quam venenatis nec euismod sit amet egestas placerat est Pellentesque habitant morbi tristique senectus et netus et malesuada fames ac turpis egestas Cras id elit integer quis urna Ut ante enim</p>
  </div>
  <div class="btn-outline abs" style="left:662px;top:1127px;width:168px;height:56px">Learn More</div>
</section>

<section class="how">
  <svg class="how-bg abs" width="1200" height="560" viewBox="0 0 1200 560" preserveAspectRatio="none"><path d="M0 40 C220 0 380 70 620 60 C860 50 1000 -20 1200 30 L1200 520 L0 520Z" fill="#e5e5f1"/></svg>
  <h2 class="how-title abs">HOW IT WORKS</h2>
  <svg class="abs" style="left:0;top:1470px" width="1200" height="200" viewBox="0 0 1200 200" fill="none">
    <path d="M278 56 C350 40 420 40 480 100" stroke="#8a8ca8" stroke-width="2" stroke-dasharray="3 6"/>
    <path d="M597 140 C660 150 720 120 788 80" stroke="#8a8ca8" stroke-width="2" stroke-dasharray="3 6"/>
    <path d="M388 38l30 6-28 8 6-7z" stroke="#2f7d3b" stroke-width="2"/>
    <path d="M680 150l32-8-24 18 0-9z" stroke="#2f7d3b" stroke-width="2"/>
    <circle cx="219" cy="67" r="52" fill="#fff" stroke="#2f7d3b" stroke-width="6"/>
    <rect x="196" y="48" width="46" height="32" rx="3" stroke="#2b2d6e" stroke-width="3"/><path d="M210 88h18M219 80v8" stroke="#2b2d6e" stroke-width="3"/>
    <circle cx="538" cy="130" r="52" fill="#fff" stroke="#2f7d3b" stroke-width="6"/>
    <rect x="514" y="114" width="48" height="34" rx="3" stroke="#2b2d6e" stroke-width="3"/><path d="M514 116l24 18 24-18" stroke="#2b2d6e" stroke-width="3"/>
    <circle cx="845" cy="67" r="52" fill="#fff" stroke="#2b2d6e" stroke-width="6"/>
    <rect x="822" y="40" width="46" height="48" rx="4" stroke="#2b2d6e" stroke-width="3"/><path d="M822 58h46M832 48h26M830 96v-8M860 96v-8" stroke="#2b2d6e" stroke-width="3"/>
  </svg>
  <div class="step-num abs" style="left:143px;top:1590px">1</div>
  <div class="abs" style="left:190px;top:1604px;width:190px"><div class="step-head">Simple, Easy Booking</div><div class="step-text">Call 1800 555 019 or click here to get started with your instant quote</div></div>
  <div class="step-num abs" style="left:448px;top:1652px">2</div>
  <div class="abs" style="left:505px;top:1665px;width:210px"><div class="step-head">Instant Confirmation</div><div class="step-text">Receive your booking details and a 30 minute courtesy call before drop off</div></div>
  <div class="step-num abs" style="left:760px;top:1590px">3</div>
  <div class="abs" style="left:817px;top:1612px;width:220px"><div class="step-head">Gone When Your Ready!</div><div class="step-text">Let us know and your bin will be gone within 24hrs</div></div>
</section>

<section class="save">
  <svg class="save-bg abs" width="1200" height="610" viewBox="0 0 1200 610" preserveAspectRatio="none">
    <path d="M0 30 C200 -10 420 60 640 40 L640 600 L0 600Z" fill="#2f7d3b"/>
    <path d="M560 44 C760 20 960 90 1200 30 L1200 600 L560 600Z" fill="#2b2d6e"/>
    <path d="M0 500 C260 620 520 560 760 520 C960 490 1100 530 1200 560 L1200 610 L0 610Z" fill="#fff"/>
  </svg>
  <h2 class="save-title abs">SAVE TIME. SAVE MONEY.</h2>
  <p class="save-text abs">Lorem ipsum dolor sit amet, consectetur adipiscing elit. Morbi neque odio, luctus ac libero eget, accumsan pellentesque felis. Proin ullamcorper tortor vitae sodales efficitur. Pellentesque aliquet augue eget eleifend congue. Integer non lectus mattis massa rhoncus varius ac ac nulla.</p>
  <div class="btn-green abs">READ MORE</div>

  <div class="feature abs" style="left:601px;top:1837px;width:217px;height:269px">
    <svg width="86" height="86" viewBox="0 0 86 86"><circle cx="43" cy="43" r="43" fill="#2f7d3b"/><path d="M31 28h24l-3 34H34z" fill="none" stroke="#fff" stroke-width="3"/><path d="M28 28h30" stroke="#fff" stroke-width="3"/><circle cx="43" cy="44" r="6" fill="none" stroke="#fff" stroke-width="2.5"/></svg>
    <h3>Any Bin, Anytime,<br>Anywhere</h3><p>We connect you with local companies Australia wide; for faster</p>
  </div>
  <div class="feature abs" style="left:840px;top:1892px;width:214px;height:269px">
    <svg width="86" height="86" viewBox="0 0 86 86"><circle cx="43" cy="43" r="43" fill="#2f7d3b"/><path d="M43 20l18 7v14c0 12-8 20-18 24-10-4-18-12-18-24V27z" fill="none" stroke="#fff" stroke-width="3"/><path d="M34 43l7 7 12-13" fill="none" stroke="#fff" stroke-width="3"/></svg>
    <h3>Service Guaranteed</h3><p>Want to speak to someone when it suits you? We answer the phones and return calls from 7:30am</p>
  </div>
  <div class="feature abs" style="left:601px;top:2136px;width:217px;height:267px">
    <svg width="86" height="86" viewBox="0 0 86 86"><circle cx="43" cy="43" r="43" fill="#2f7d3b"/><circle cx="43" cy="43" r="22" fill="none" stroke="#fff" stroke-width="3"/><text x="43" y="53" text-anchor="middle" font-family="Lato,sans-serif" font-size="28" font-weight="700" fill="#fff">$</text></svg>
    <h3>Best Pricing</h3><p>We've done the hard work behind the scenes, so with one click you have your best priced, local skip</p>
  </div>
  <div class="feature abs" style="left:840px;top:2189px;width:214px;height:269px">
    <svg width="86" height="86" viewBox="0 0 86 86"><circle cx="43" cy="43" r="43" fill="#2f7d3b"/><path d="M20 40l10-10 13 6 13-6 10 10-14 14c-3 3-6 3-9 0z" fill="none" stroke="#fff" stroke-width="3" stroke-linejoin="round"/></svg>
    <h3>First Class Supply<br>Partners</h3><p>Our local supply partners are the best in the business and share our passion for making you happy</p>
  </div>
</section>

<section class="testimonials">
  <h2 class="testi-title abs">TESTIMONIALS</h2>
  <div class="quote-mark abs">&ldquo;</div>
  <svg class="abs" style="left:170px;top:2632px" width="30" height="50" viewBox="0 0 30 50"><path d="M26 2L4 25l22 23" fill="none" stroke="#9a9bb0" stroke-width="3"/></svg>
  <svg class="abs" style="left:1016px;top:2632px" width="30" height="50" viewBox="0 0 30 50"><path d="M4 2l22 23L4 48" fill="none" stroke="#9a9bb0" stroke-width="3"/></svg>
  <p class="testi-text abs">The Tallow Crate Rentals Australia - 4 cubic bin hire fee was cost competitive; communication with admin &amp; delivery driver was effective; delivery of bin was on time and placed where required, and bin collection occurred as agreed. No problems encountered.</p>
  <div class="testi-label abs">SERVICE EXCELLENCE</div>
  <div class="stars abs">
    <svg width="126" height="24" viewBox="0 0 126 24" fill="#f2a516"><g id="s"><path d="M12 1l3.4 7 7.6 1-5.5 5.3 1.3 7.6L12 18.3 5.2 21.9l1.3-7.6L1 9l7.6-1z"/></g><use href="#s" x="26"/><use href="#s" x="52"/><use href="#s" x="78"/><use href="#s" x="104"/></svg>
  </div>
</section>

<section class="ready">
  <svg class="ready-bg abs" width="1200" height="500" viewBox="0 0 1200 500" preserveAspectRatio="none" role="img" aria-label="Photo of a family moving house, tinted navy">
    <defs><linearGradient id="rg" x1="0" y1="0" x2="1" y2="1"><stop offset="0" stop-color="#2b2d6e"/><stop offset=".6" stop-color="#3a3c70"/><stop offset="1" stop-color="#4a4b72"/></linearGradient></defs>
    <path d="M0 30 C250 -10 520 50 760 30 C960 10 1080 0 1200 20 L1200 460 C950 420 720 500 420 470 C220 450 100 480 0 470Z" fill="url(#rg)"/>
  </svg>
  <h2 class="ready-title abs">WE'RE READY TO GO!</h2>
  <p class="ready-text abs">TO BOOK, ASK QUESTIONS OR JUST FOR A CHAT, CALL US<br>7 DAYS A WEEK, 7.30AM TO 8PM</p>
  <div class="search ready-search abs"><span>Enter Postcode or Suburb</span><b>Search</b></div>
  <div class="btn-ghost abs">Call Now</div>
</section>

<footer class="site-footer">
  <div class="footer-skyline abs" role="img" aria-label="Faint line drawing of a city skyline"></div>
  <div class="brand footer-brand abs"><span class="brand-mark"></span><span class="brand-name">TALLOW CRATE RENTALS AUSTRALIA</span></div>
  <p class="footer-about abs">Lorem ipsum dolor sit amet consectetuer adipiscing elit Nam cursus Morbi ut mi Nullam enim leo</p>
  <div class="footer-col abs" style="left:463px;top:3420px"><h4>QUICK LINKS</h4><ul><li>Sydney</li><li>Melbourne</li><li>Brisbane</li><li>Perth</li><li>Adelaide</li><li>Canberra</li></ul></div>
  <div class="footer-col abs" style="left:621px;top:3420px"><h4>RESOURCES</h4><ul><li>Waste Types</li><li>Skip Bin Sizes</li><li>Refund Policy</li><li>Pay Later with PayNest</li><li>FAQ</li><li>Privacy</li></ul></div>
  <div class="footer-col footer-news abs" style="left:803px;top:3420px"><h4>LATEST INDUSTRY NEWS</h4><p>Sign up for the latest news, offers from TALLOW CRATE RENTALS AUSTRALIA</p></div>
  <div class="email abs">Email address</div>
  <div class="btn-sub abs">Subscribe</div>
  <div class="rule abs"></div>
  <p class="copyright abs">© 2019 Company Name&nbsp; All right reserved</p>
  <div class="social abs"><i></i><i></i><i></i></div>
</footer>

</body>
</html>
```